We need letterhead, Business Cards, and envelops designed. We have attached a design of our logo and a sample of letterhead idea that was started but never perfected, it is only an idea for the letterhead if you can design something better we may love that also we are open to change.
We want a design that looks professional in style. we are a non profit trade association in the construction industry. the green color in the attached design represent green building, and we like that. also if you just want to enhance the letterhead sample that we attached that would be fine also.
Thanks and good luck
also the name that should show on the first business cards should be Morgan Feltwick, Director are web address is www.pvtrn.org

```html
<!DOCTYPE html>
<html lang="en">
<head>
<meta charset="utf-8">
<title>PVTRN Letterhead</title>
<link rel="stylesheet" href="https://fonts.googleapis.com/css2?family=Didact+Gothic&display=swap">
<style>
  :root {
    --ink: #111111;
    --paper: #ffffff;
    --leaf: #3f7a1f;
    --band: #050505;
    --text-muted: #1a1a1a;
  }
  html, body {
    margin: 0;
    padding: 0;
    background: var(--paper);
    overflow: hidden;
  }
  .letterhead {
    position: relative;
    width: 927px;
    height: 1200px;
    background: var(--paper);
    overflow: hidden;
    font-family: "Didact Gothic", "Century Gothic", sans-serif;
    color: var(--ink);
  }
  .brand-name {
    position: absolute;
    top: 50px;
    left: 0;
    width: 100%;
    margin: 0;
    text-align: center;
    font-size: 76px;
    font-weight: 400;
    letter-spacing: 4px;
    line-height: 1;
    color: var(--ink);
  }
  .contact {
    position: absolute;
    top: 1108px;
    font-size: 13.5px;
    letter-spacing: 1.6px;
    line-height: 18px;
    color: var(--text-muted);
  }
  .contact-address {
    left: 71px;
  }
  .contact-lines {
    left: 246px;
    list-style: none;
    margin: 0;
    padding: 0;
  }
  .contact-lines li {
    display: flex;
    align-items: center;
    height: 18px;
  }
  .contact-icon {
    width: 12px;
    height: 12px;
    margin-right: 25px;
    margin-left: 1px;
    flex: none;
  }
  .contact-icon * {
    fill: none;
    stroke: var(--leaf);
    stroke-width: 1.4;
  }
  .footer-band {
    position: absolute;
    left: 0;
    bottom: 0;
    width: 927px;
    height: 44px;
  }
  .footer-band .band-dark { fill: var(--band); }
  .footer-band .band-green { fill: var(--leaf); }
</style>
</head>
<body>
<main class="letterhead">
  <h1 class="brand-name">PVTRN</h1>

  <address class="contact contact-address">
    address<br>
    4321 first street<br>
    anytown, State ZIP
  </address>

  <ul class="contact contact-lines">
    <li>
      <svg class="contact-icon" viewBox="0 0 12 12" aria-hidden="true">
        <path d="M1.5 4.5 Q6 1 10.5 4.5"/>
        <rect x="3" y="5.5" width="6" height="5" rx="1"/>
        <circle cx="6" cy="8" r="1"/>
      </svg>
      123-456-7890
    </li>
    <li>
      <svg class="contact-icon" viewBox="0 0 12 12" aria-hidden="true">
        <rect x="3" y="1" width="6" height="3"/>
        <rect x="1" y="4" width="10" height="4.5" rx="1"/>
        <rect x="3" y="7" width="6" height="4"/>
      </svg>
      123-456-7891
    </li>
    <li>
      <svg class="contact-icon" viewBox="0 0 12 12" aria-hidden="true">
        <circle cx="6" cy="6" r="5"/>
        <ellipse cx="6" cy="6" rx="2.2" ry="5"/>
        <path d="M1 6 H11"/>
      </svg>
      www.pvtrn.org
    </li>
  </ul>

  <svg class="footer-band" viewBox="0 0 927 44" aria-hidden="true">
    <rect class="band-dark" x="0" y="27" width="927" height="17"/>
    <polygon class="band-green" points="501,1 927,1 927,44 478,44"/>
  </svg>
</main>
</body>
</html>
```